Business card for law firm

Need business card for new law firm. Think confident, authoritative, conservative, but not stuffy or old-fashioned.

Contact Information for Business Card

Content for card - logo (uploaded), plus the following:

Paul Whitcombe (larger font)
Managing Partner (larger font, but not as large as name)
Level 9, 7 Ferris Lane
Sydney NSW 2000
Main Tel 02 9364 2710
Direct Tel 02 8472 3159
Email paul@qvlegal.com.au
www.qvlegal.com.au

Letterhead design should include logo plus:
Level 9, 7 Ferris Lane
Sydney NSW 2000
Tel 02 8472 3159
www.qvlegal.com.au

```html
<!DOCTYPE html>
<html lang="en">
<head>
<meta charset="utf-8">
<title>Quayvale Lawyers – Business Card</title>
<link href="https://fonts.googleapis.com/css2?family=Cinzel:wght@400;600&family=EB+Garamond:wght@400&display=swap" rel="stylesheet">
<style>
  :root {
    --navy: #0f1f5c;
    --ink: #1c1c1c;
    --grey: #6f6f6f;
    --paper: #ffffff;
    --stage: #2b2b2b;
    --rule: #d6d6d6;
  }
  * { box-sizing: border-box; margin: 0; padding: 0; }
  html, body {
    width: 1200px; height: 960px; overflow: hidden;
    background: var(--stage);
  }
  .sheet {
    width: 1200px; height: 960px;
    display: flex; flex-direction: column; align-items: center; justify-content: center;
    gap: 48px;
  }
  .card {
    position: relative;
    width: 700px; height: 400px;
    box-shadow: 0 10px 30px rgba(0,0,0,.45);
  }
  .card__frame {
    position: absolute; inset: 16px;
    pointer-events: none;
  }

  /* Back side */
  .card--back { background: var(--navy); }
  .card--back .card__frame { border: 1.5px solid rgba(255,255,255,.85); }
  .card--back .brand { color: var(--paper); }
  .card--back .brand__mark { background: var(--paper); }
  .card--back .brand-wrap {
    position: absolute; inset: 0;
    display: flex; align-items: center; justify-content: center;
  }

  /* Front side */
  .card--front { background: var(--paper); }
  .card--front .card__frame { border: 2px solid var(--ink); }
  .card--front .brand-wrap {
    position: absolute; left: 16px; top: 16px; bottom: 16px; width: 340px;
    display: flex; align-items: center; justify-content: center;
  }
  .card--front .brand { color: var(--ink); }
  .card--front .brand__mark { background: var(--navy); }
  .divider {
    position: absolute; left: 364px; top: 56px; bottom: 56px;
    width: 1px; background: var(--rule);
  }

  /* Brand lockup */
  .brand {
    display: flex; flex-direction: column; align-items: center;
    font-family: "Cinzel", serif; font-weight: 400;
  }
  .brand__mark { width: 62px; height: 62px; margin-bottom: 18px; }
  .brand__name { font-size: 38px; letter-spacing: 1px; line-height: 1; }
  .brand__sub { font-size: 13px; letter-spacing: 12px; margin-top: 8px; padding-left: 12px; }

  /* Contact block */
  .contact {
    position: absolute; left: 392px; top: 92px; right: 30px;
    font-family: "EB Garamond", serif; color: var(--grey);
  }
  .contact__name {
    font-family: "Cinzel", serif; font-weight: 600;
    font-size: 23px; color: var(--navy); letter-spacing: .5px; line-height: 1.1;
  }
  .contact__role {
    font-family: "Cinzel", serif; font-size: 14px; color: var(--grey);
    letter-spacing: .8px; margin-bottom: 16px;
  }
  .contact__address { font-size: 16px; line-height: 1.3; margin-bottom: 14px; }
  .contact__list { list-style: none; font-size: 16px; line-height: 1.55; }
  .contact__list li { display: flex; align-items: center; gap: 10px; padding-left: 22px; }
  .icon { width: 13px; height: 13px; fill: var(--navy); flex: none; }
</style>
</head>
<body>
<main class="sheet">

  <section class="card card--back" aria-label="Card back">
    <div class="card__frame"></div>
    <div class="brand-wrap">
      <div class="brand">
        <div class="brand__mark"></div>
        <div class="brand__name">QUAYVALE</div>
        <div class="brand__sub">LAWYERS</div>
      </div>
    </div>
  </section>

  <section class="card card--front" aria-label="Card front">
    <div class="card__frame"></div>
    <div class="brand-wrap">
      <div class="brand">
        <div class="brand__mark"></div>
        <div class="brand__name">QUAYVALE</div>
        <div class="brand__sub">LAWYERS</div>
      </div>
    </div>
    <div class="divider"></div>

    <div class="contact">
      <div class="contact__name">PAUL WHITCOMBE</div>
      <div class="contact__role">MANAGING PARTNER</div>
      <div class="contact__address">Level 9, 7 Ferris Lane<br>Sydney NSW 2000</div>
      <ul class="contact__list">
        <li><svg class="icon" viewBox="0 0 16 16"><path d="M3.5 1.5l2.5 0 1 3.5-1.7 1.2c.8 1.8 2.2 3.2 4 4l1.2-1.7 3.5 1v2.5c0 .8-.7 1.5-1.5 1.5C6.6 13.5 2.5 9.4 2 3c0-.8.7-1.5 1.5-1.5z"/></svg>02 9364 2710</li>
        <li><svg class="icon" viewBox="0 0 16 16"><path d="M3.5 1.5l2.5 0 1 3.5-1.7 1.2c.8 1.8 2.2 3.2 4 4l1.2-1.7 3.5 1v2.5c0 .8-.7 1.5-1.5 1.5C6.6 13.5 2.5 9.4 2 3c0-.8.7-1.5 1.5-1.5z"/></svg>02 8472 3159</li>
        <li><svg class="icon" viewBox="0 0 16 16"><path d="M1 3h14v10H1z M1.8 3.6L8 8.6l6.2-5" stroke="#fff" stroke-width="1.2"/></svg>paul@qvlegal.com.au</li>
        <li><svg class="icon" viewBox="0 0 16 16"><circle cx="8" cy="8" r="7"/><path d="M1 8h14M8 1c-2.5 3-2.5 11 0 14M8 1c2.5 3 2.5 11 0 14" stroke="#fff" stroke-width="1" fill="none"/></svg>www.qvlegal.com.au</li>
      </ul>
    </div>
  </section>

</main>
</body>
</html>
```